Heron Loan Partners Business Card

We need a business card design for our mortgage servicing company. In addition to servicing the loans of homeowners, we help homeowners with purchasing their homes and any mortgage refinancing. We would like to see designs that use the colors in the logo attached below (gold-ish yellow and navy blue), and any other design you deem fit! The design should communicate a simpler life with smart mortgages provided by Heron.

```html
<!DOCTYPE html>
<html lang="en">
<head>
<meta charset="utf-8">
<title>Heron Loan Partners Business Card</title>
<link href="https://fonts.googleapis.com/css2?family=Montserrat:wght@400;500;700&display=swap" rel="stylesheet">
<style>
  :root {
    --navy: #25215a;
    --gold: #e2b43c;
    --white: #ffffff;
    --backdrop: #e6e6e9;
  }
  * { margin: 0; padding: 0; box-sizing: border-box; }
  html, body {
    width: 1200px; height: 900px; overflow: hidden;
    background: var(--backdrop);
    font-family: "Montserrat", Arial, sans-serif;
  }
  .card {
    position: absolute; left: 250px;
    width: 700px; height: 400px;
    overflow: hidden;
    box-shadow: 0 6px 18px rgba(0,0,0,0.18);
  }
  .card-front { top: 35px; background: var(--navy); }
  .card-back { top: 465px; background: var(--white); }

  .front-name {
    position: absolute; left: 0; right: 0; top: 170px;
    text-align: center;
    color: var(--gold);
    font-weight: 700; font-size: 52px; letter-spacing: 0.5px;
  }
  .back-wave { position: absolute; inset: 0; }
  .back-name {
    position: absolute; left: 50px; top: 140px;
    color: var(--navy);
    font-weight: 700; font-size: 30px;
  }
  .contact {
    position: absolute; right: 30px; top: 125px;
    width: 240px;
    color: var(--white);
    text-align: right;
  }
  .contact-person {
    font-weight: 700; font-size: 17px; letter-spacing: 0.5px;
    text-transform: uppercase;
  }
  .contact-role { font-size: 13px; margin-top: 2px; margin-bottom: 18px; }
  .contact-row {
    display: flex; justify-content: flex-end; align-items: center;
    gap: 10px;
    font-size: 13px; line-height: 1.45;
  }
  .contact-row svg { width: 14px; height: 14px; flex: none; }
  .contact-address { margin-bottom: 6px; padding-right: 24px; }
</style>
</head>
<body>
  <section class="card card-front">
    <div class="front-name">Heron Loan Partners</div>
  </section>

  <section class="card card-back">
    <svg class="back-wave" viewBox="0 0 700 400" width="700" height="400" aria-hidden="true">
      <path d="M560,0 C470,30 420,100 395,180 C360,290 280,360 110,400 L700,400 L700,0 Z" fill="var(--navy)"/>
      <path d="M584,0 C494,30 444,100 419,180 C384,290 304,362 134,400" fill="none" stroke="var(--white)" stroke-width="14"/>
      <path d="M584,0 C494,30 444,100 419,180 C384,290 304,362 134,400" fill="none" stroke="var(--gold)" stroke-width="8"/>
    </svg>

    <div class="back-name">Heron Loan Partners</div>

    <div class="contact">
      <div class="contact-person">Dana Whitcombe</div>
      <div class="contact-role">Owner</div>
      <div class="contact-row contact-address">482 Brookline Ave, Ste 200,<br>Fairhaven, TX 75021</div>
      <div class="contact-row">555.014.2290
        <svg viewBox="0 0 16 16"><path d="M3 1.5 L6 1.5 L7 5 L5.3 6.3 C6.2 8.2 7.8 9.8 9.7 10.7 L11 9 L14.5 10 L14.5 13 C14.5 14 13.7 14.5 13 14.5 C6.9 14 2 9.1 1.5 3 C1.5 2.2 2.1 1.5 3 1.5 Z" fill="var(--gold)"/></svg>
      </div>
      <div class="contact-row">info@heronloanpartners.com
        <svg viewBox="0 0 16 16"><rect x="1" y="3" width="14" height="10" rx="1" fill="var(--gold)"/><path d="M1.5 3.5 L8 9 L14.5 3.5" fill="none" stroke="var(--navy)" stroke-width="1.2"/></svg>
      </div>
      <div class="contact-row">www.heronloanpartners.com
        <svg viewBox="0 0 16 16"><circle cx="8" cy="8" r="7" fill="var(--gold)"/><path d="M1 8 H15 M8 1 C5 4 5 12 8 15 M8 1 C11 4 11 12 8 15" fill="none" stroke="var(--navy)" stroke-width="0.9"/></svg>
      </div>
    </div>
  </section>
</body>
</html>
```